FunBrixo Business Card

We need a business card design for our company. We sell construction-themed amusement rides for kids.

Contact Information for Business Card

Contact info on business card should include:
Carl Dunning
Co-Founder & COO
(833) 571-FUNBRIX
Carl@funbrixo-demo.com
www.funbrixo-demo.com

```html
<!DOCTYPE html>
<html lang="en">
<head>
<meta charset="utf-8">
<title>FunBrixo Business Card</title>
<link rel="stylesheet" href="https://fonts.googleapis.com/css2?family=Open+Sans:wght@400;600;700;800&display=swap">
<style>
  :root {
    --backdrop: #5a5b60;
    --card-black: #1b1b1b;
    --card-white: #ffffff;
    --brand-purple: #983f99;
    --brand-orange: #ee6a3c;
    --text-light: #ffffff;
    --card-shadow: rgba(0, 0, 0, 0.35);
  }
  * { margin: 0; padding: 0; box-sizing: border-box; }
  html, body {
    width: 1200px;
    height: 811px;
    overflow: hidden;
    background: var(--backdrop);
    font-family: "Open Sans", Arial, sans-serif;
  }
  .canvas {
    position: relative;
    width: 1200px;
    height: 811px;
  }
  .card {
    position: absolute;
    top: 251px;
    width: 540px;
    height: 309px;
    overflow: hidden;
    box-shadow: 0 14px 30px var(--card-shadow);
  }
  /* Back side */
  .card-back {
    left: 45px;
    background: var(--card-black);
    display: flex;
    align-items: center;
    justify-content: center;
  }
  .card-back .wordmark { color: var(--text-light); }

  .wordmark {
    font-weight: 800;
    font-size: 52px;
    letter-spacing: -0.5px;
    line-height: 1;
  }

  /* Front side */
  .card-front {
    left: 615px;
    background: var(--card-white);
  }
  .front-logo-area {
    position: absolute;
    left: 0; top: 0;
    width: 100%;
    height: 138px;
    display: flex;
    align-items: center;
    justify-content: center;
  }
  .card-front .wordmark {
    color: var(--brand-orange);
    font-size: 48px;
  }
  .name-band {
    position: absolute;
    left: 0; top: 138px;
    width: 100%;
    height: 54px;
    background: var(--brand-purple);
    display: flex;
    align-items: center;
    justify-content: center;
    color: var(--text-light);
  }
  .person-name {
    font-weight: 700;
    font-size: 19px;
  }
  .person-role {
    font-weight: 400;
    font-size: 11.5px;
    margin-left: 5px;
  }
  .band-divider {
    position: absolute;
    left: 0; top: 192px;
    width: 100%;
    height: 5px;
    background: var(--card-white);
  }
  .contact-band {
    position: absolute;
    left: 0; top: 197px;
    width: 100%;
    height: 112px;
    background: var(--brand-orange);
  }
  .contact-list {
    position: absolute;
    left: 0; right: 0;
    top: 44px;
    display: flex;
    justify-content: space-between;
    padding: 0 26px 0 28px;
    list-style: none;
    color: var(--text-light);
    font-size: 11.5px;
    font-weight: 400;
  }
  .contact-item {
    display: flex;
    align-items: center;
    gap: 6px;
  }
  .contact-icon {
    width: 12px;
    height: 12px;
    flex: none;
  }
</style>
</head>
<body>
<main class="canvas">

  <section class="card card-back" aria-label="Business card, back">
    <span class="wordmark">FunBrixo</span>
  </section>

  <section class="card card-front" aria-label="Business card, front">
    <div class="front-logo-area">
      <span class="wordmark">FunBrixo</span>
    </div>

    <div class="name-band">
      <span class="person-name">Carl Dunning,</span>
      <span class="person-role">Co-Founder &amp; COO</span>
    </div>

    <div class="band-divider"></div>

    <div class="contact-band">
      <ul class="contact-list">
        <li class="contact-item">
          <svg class="contact-icon" viewBox="0 0 12 12" aria-hidden="true">
            <rect x="3" y="0.5" width="6" height="11" rx="1" fill="none" stroke="#fff" stroke-width="1.2"/>
            <circle cx="6" cy="9.5" r="0.7" fill="#fff"/>
          </svg>
          <span>(833) 571-FUNBRIX</span>
        </li>
        <li class="contact-item">
          <svg class="contact-icon" viewBox="0 0 12 12" aria-hidden="true">
            <rect x="0.5" y="2.5" width="11" height="7.5" fill="#fff"/>
            <path d="M0.8 2.8 L6 7 L11.2 2.8" fill="none" stroke="#ee6a3c" stroke-width="1"/>
          </svg>
          <span>Carl@funbrixo-demo.com</span>
        </li>
        <li class="contact-item">
          <svg class="contact-icon" viewBox="0 0 12 12" aria-hidden="true">
            <circle cx="6" cy="6" r="5" fill="none" stroke="#fff" stroke-width="1.1"/>
            <ellipse cx="6" cy="6" rx="2.2" ry="5" fill="none" stroke="#fff" stroke-width="0.9"/>
            <line x1="1" y1="6" x2="11" y2="6" stroke="#fff" stroke-width="0.9"/>
          </svg>
          <span>www.funbrixo-demo.com</span>
        </li>
      </ul>
    </div>
  </section>

</main>
</body>
</html>
```